Automotive component supplier needs a business card design

We need a business card design for our company called Velran Global Components Ltd based in the UK. We are a supplier of interior and exterior components to premium car manufacturers such as Corvel Ashby, Hadley Fenn, Marquist and Tavarelli. We would like to see a modern business card design that uses the colour blue.

Target Market(s)

Premium automotive car manufacturers.

Industry/Entity Type

Automotive

Contact Information for Business Card

Company Name : Velran Global Components Limited
Address: 17 Marlow Yard, Upper Heath, Warwick, CV31 8QL, United Kingdom
Web Address : www.velrancomponents-example.co.uk

Font styles to use
Other font styles liked:
• Helvetica

Colors
3176b5
0255a3
85acd3
cfdeed
cee9f5
85cae6
34a6d7
0692cd
9bcb3c

Requirements
Must have
• Clear company logo and a mixture of blue colours.
Nice to have
• A high quality modern image.
Should not have
• Multiple colours.

```html
<!DOCTYPE html>
<html lang="en">
<head>
<meta charset="utf-8">
<title>Velran Global Components – Business Card</title>
<link rel="stylesheet" href="https://fonts.googleapis.com/css2?family=Exo+2:wght@400;600;700&display=swap">
<style>
  :root {
    --blue-deep: #0255a3;
    --blue-mid: #3176b5;
    --blue-bright: #0692cd;
    --blue-sky: #34a6d7;
    --blue-soft: #85cae6;
    --blue-pale: #eef6fb;
    --green: #9bcb3c;
    --white: #ffffff;
    --page: #e9edf1;
  }
  * { margin: 0; padding: 0; box-sizing: border-box; }
  html, body { width: 1200px; height: 950px; overflow: hidden; }
  body {
    background: var(--page);
    font-family: "Exo 2", "Helvetica Neue", Arial, sans-serif;
    position: relative;
  }
  .card {
    position: absolute;
    top: 125px;
    width: 400px;
    height: 700px;
    overflow: hidden;
    box-shadow: 0 10px 30px rgba(2, 85, 163, 0.18);
    background: var(--white);
  }
  .card--front { left: 160px; }
  .card--back { left: 640px; }
  .card__art { position: absolute; inset: 0; }

  /* Company name, set plainly in the text face */
  .company-name {
    color: var(--blue-mid);
    font-weight: 600;
    letter-spacing: 0;
    white-space: nowrap;
    text-align: center;
  }

  /* Front */
  .card--front .company-name {
    position: absolute;
    top: 92px;
    left: 0;
    width: 100%;
    font-size: 27px;
  }

  .person { position: absolute; top: 238px; width: 100%; text-align: center; }
  .person__name { color: var(--blue-bright); font-weight: 700; font-size: 24px; letter-spacing: 1.5px; }
  .person__role { color: var(--green); font-size: 17px; margin-top: 2px; }

  .address {
    position: absolute; top: 440px; width: 100%;
    text-align: center; color: var(--white); font-size: 17px; line-height: 1.35;
  }
  .divider { width: 46px; height: 1px; background: var(--white); margin: 18px auto 16px; opacity: .9; }
  .contacts { list-style: none; color: var(--white); font-size: 15px; line-height: 1.6; padding-left: 34px; text-align: left; }
  .contacts li { display: flex; align-items: center; gap: 10px; }
  .contacts svg { width: 15px; height: 15px; flex: none; }

  /* Back */
  .back-pattern { position: absolute; inset: 0; background: linear-gradient(160deg, var(--blue-pale), var(--white)); }
  .card--back .company-name {
    position: absolute;
    top: 50%;
    left: 50%;
    font-size: 46px;
    transform: translate(-50%, -50%) rotate(90deg);
  }
  .back-web {
    position: absolute; top: 50%; left: 30px;
    transform: translate(-50%, -50%) rotate(90deg);
    color: var(--blue-mid); font-size: 15px; letter-spacing: 4px; white-space: nowrap;
  }
</style>
</head>
<body>

<section class="card card--front" aria-label="Business card front">
  <svg class="card__art" viewBox="0 0 400 700" aria-hidden="true">
    <defs>
      <linearGradient id="frontBlue" x1="0" y1="0" x2="1" y2="1">
        <stop offset="0" stop-color="#34a6d7"/>
        <stop offset="1" stop-color="#0692cd"/>
      </linearGradient>
    </defs>
    <rect width="400" height="700" fill="url(#frontBlue)"/>
    <polygon points="0,420 400,250 400,330 0,560" fill="#85cae6" opacity=".18"/>
    <path d="M0 0 H400 V300 L232 392 Q200 410 168 392 L0 300 Z" fill="#ffffff"/>
    <rect width="400" height="10" fill="#9bcb3c"/>
  </svg>

  <div class="company-name">Velran Global Components</div>

  <div class="person">
    <div class="person__name">DANIEL HARROW</div>
    <div class="person__role">CEO / Founder</div>
  </div>

  <div class="address">
    17 Marlow Yard, Upper Heath<br>
    Warwick, CV31 8QL<br>
    United Kingdom
    <div class="divider"></div>
    <ul class="contacts">
      <li><svg viewBox="0 0 16 16"><path d="M4 1 L6.5 4 L5 6 Q6.5 9.5 10 11 L12 9.5 L15 12 L13 15 Q5 14 1 3 Z" fill="#fff"/></svg>889 512 0473</li>
      <li><svg viewBox="0 0 16 16"><rect x="4" y="1" width="8" height="14" rx="1.5" fill="none" stroke="#fff" stroke-width="1.6"/><circle cx="8" cy="12.5" r="1" fill="#fff"/></svg>536 710 2285</li>
      <li><svg viewBox="0 0 16 16"><rect x="1" y="3" width="14" height="10" fill="#fff"/><path d="M1 3 L8 9 L15 3" fill="none" stroke="#0692cd" stroke-width="1.3"/></svg>daniel@velrancomponents-example.co.uk</li>
      <li><svg viewBox="0 0 16 16"><circle cx="8" cy="8" r="6.5" fill="none" stroke="#fff" stroke-width="1.5"/><path d="M1.5 8 H14.5 M8 1.5 Q4 8 8 14.5 Q12 8 8 1.5" fill="none" stroke="#fff" stroke-width="1.2"/></svg>www.velrancomponents-example.co.uk</li>
    </ul>
  </div>
</section>

<section class="card card--back" aria-label="Business card back">
  <div class="back-pattern" role="img" aria-label="Faint repeating pale blue background pattern"></div>
  <div class="company-name">Velran Global Components</div>
  <div class="back-web">www.velrancomponents-example.co.uk</div>
</section>

</body>
</html>
```